Corvel Capital LLC

Need Professional Business cards for New Investment Fund

Target Market(s)

High Quality investors

Industry/Entity Type

Financial

Contact Information for Business Card

Phone Number +1 555 284 6190
Name Lukas Varenko
Title Fund Manager
email lv@FundCorvel.com
Website www.FundCorvel.com

Colors

Designer to choose colors to be used in the design.

Requirements
Must have
• Must have our Logo and all of the above. Must be made so lettering and loge can be raised

```html
<!DOCTYPE html>
<html lang="en">
<head>
<meta charset="utf-8">
<title>Corvel Capital LLC – Business Card</title>
<link rel="stylesheet" href="https://fonts.googleapis.com/css2?family=Montserrat:wght@400;500;600;700&display=swap">
<style>
  :root {
    --backdrop: #2f2624;
    --card: #333436;
    --card-edge: #27d11a;
    --accent: #2fd41c;
    --ink: #f2f2f2;
    --ink-soft: #d9d9d9;
    --emboss: #3e3f42;
    --rule: #bfbfbf;
  }
  * { box-sizing: border-box; margin: 0; padding: 0; }
  html, body {
    width: 1200px;
    height: 800px;
    overflow: hidden;
    background: var(--backdrop);
    font-family: "Montserrat", Arial, sans-serif;
  }
  .stage {
    position: relative;
    width: 1200px;
    height: 800px;
    display: flex;
    align-items: center;
    justify-content: center;
    gap: 40px;
  }
  .card {
    position: relative;
    width: 520px;
    height: 300px;
    background: var(--card);
    border: 2px solid var(--card-edge);
    border-radius: 3px;
  }

  /* Back side */
  .card-back {
    display: flex;
    align-items: center;
    justify-content: center;
  }
  .back-wordmark {
    font-size: 40px;
    font-weight: 700;
    letter-spacing: 1px;
    line-height: 1.1;
    text-align: center;
    color: var(--emboss);
  }

  /* Front side */
  .card-front {
    display: flex;
    align-items: center;
    padding: 0 36px 0 48px;
  }
  .brand {
    display: flex;
    align-items: center;
    gap: 10px;
    width: 160px;
    flex: none;
  }
  .brand-mark {
    width: 14px;
    height: 14px;
    flex: none;
    background: var(--accent);
  }
  .brand-name {
    font-size: 20px;
    font-weight: 700;
    line-height: 1.15;
    color: var(--ink);
  }
  .divider {
    width: 1px;
    height: 110px;
    flex: none;
    background: var(--rule);
    margin: 0 24px 0 8px;
  }
  .details { color: var(--ink); }
  .person-name {
    font-size: 18px;
    font-weight: 700;
    letter-spacing: 0.6px;
    text-transform: uppercase;
    color: var(--accent);
    white-space: nowrap;
  }
  .person-title {
    font-size: 13px;
    font-weight: 500;
    color: var(--ink-soft);
    margin: 2px 0 12px;
  }
  .contact-list { list-style: none; }
  .contact-list li {
    display: flex;
    align-items: center;
    gap: 8px;
    font-size: 13px;
    font-weight: 500;
    line-height: 21px;
    white-space: nowrap;
  }
  .contact-icon {
    width: 12px;
    height: 12px;
    flex: none;
  }
</style>
</head>
<body>
  <main class="stage">
    <section class="card card-back" aria-label="Card back">
      <span class="back-wordmark">Corvel<br>Capital</span>
    </section>

    <section class="card card-front" aria-label="Card front">
      <div class="brand">
        <span class="brand-mark"></span>
        <span class="brand-name">Corvel<br>Capital</span>
      </div>
      <div class="divider"></div>
      <div class="details">
        <p class="person-name">Lukas Varenko</p>
        <p class="person-title">Fund Manager</p>
        <ul class="contact-list">
          <li>
            <svg class="contact-icon" viewBox="0 0 24 24" aria-hidden="true">
              <path fill="#2fd41c" d="M6.6 10.8a15.1 15.1 0 0 0 6.6 6.6l2.2-2.2c.3-.3.7-.4 1-.2 1.1.4 2.3.6 3.6.6.6 0 1 .4 1 1V20c0 .6-.4 1-1 1A17 17 0 0 1 3 4c0-.6.4-1 1-1h3.5c.6 0 1 .4 1 1 0 1.3.2 2.5.6 3.6.1.3 0 .7-.2 1z"/>
            </svg>
            +1 555 284 6190
          </li>
          <li>
            <svg class="contact-icon" viewBox="0 0 24 24" aria-hidden="true">
              <rect x="2" y="5" width="20" height="14" rx="1.5" fill="#2fd41c"/>
              <path d="M3 6l9 7 9-7" fill="none" stroke="#333436" stroke-width="2"/>
            </svg>
            lv@FundCorvel.com
          </li>
          <li>
            <svg class="contact-icon" viewBox="0 0 24 24" aria-hidden="true">
              <circle cx="12" cy="12" r="10" fill="#2fd41c"/>
              <path d="M2 12h20M12 2c3 3 3 17 0 20M12 2c-3 3-3 17 0 20" fill="none" stroke="#333436" stroke-width="1.6"/>
            </svg>
            www.FundCorvel.com
          </li>
        </ul>
      </div>
    </section>
  </main>
</body>
</html>
```